Executive Business Card for Healthcare Company [Need Today]

I need a business card design for a healthcare company. The only branding the company has thus far is a logo. The cards will be utilized by company executives. The design I envision will be vibrant and appealing but with a corporate feel. They shouldn't be too casual or playful. I would like to complete this project TODAY if possible.

Target Market(s)

Healthcare vendors, other executives in healthcare and pharmaceuticals

Industry/Entity Type

Pharmaceutical

Contact Information for Business Card

See attachment

Font styles to use
Serif
Sans Serif

Colors

Designer to choose colors to be used in the design.

```html
<!DOCTYPE html>
<html lang="en">
<head>
<meta charset="utf-8">
<title>Corvane Therapeutics – Business Card</title>
<link href="https://fonts.googleapis.com/css2?family=Arimo:wght@400;700&display=swap" rel="stylesheet">
<style>
  :root {
    --stage: #6b6b6b;
    --teal: #3bbfc8;
    --green: #6cc49a;
    --ink: #222222;
    --paper: #ffffff;
    --back: #262626;
    --muted: #8a8a8a;
  }
  * { margin: 0; padding: 0; box-sizing: border-box; }
  html, body { width: 1200px; height: 900px; overflow: hidden; }
  body {
    background: var(--stage);
    font-family: "Arimo", Arial, sans-serif;
    position: relative;
  }
  .card {
    position: absolute;
    top: 306px;
    width: 440px;
    height: 272px;
    border-radius: 12px;
    overflow: hidden;
    box-shadow: 2px 3px 4px rgba(0,0,0,0.35);
  }
  .card--front { left: 149px; background: var(--paper); }
  .card--back { left: 609px; background: var(--back); }

  .front__band {
    position: absolute; left: 0; top: 0;
    width: 100%; height: 87px;
    background: var(--teal);
  }
  .front__band-accent {
    position: absolute; right: 0; top: 0;
    width: 101px; height: 87px;
    background: var(--green);
  }
  .front__brand {
    position: absolute; left: 24px; top: 24px;
    color: var(--paper);
    font-size: 22px; font-weight: 400;
    line-height: 1.05;
    letter-spacing: 0.5px;
  }
  .front__seal {
    position: absolute; left: 279px; top: 10px;
    width: 112px; height: 112px;
    border-radius: 50%;
    background: var(--paper);
  }
  .person {
    position: absolute; left: 24px; top: 146px;
  }
  .person__name {
    font-size: 16px; font-weight: 700;
    color: var(--teal);
    letter-spacing: 0.3px;
  }
  .person__name span { color: var(--green); }
  .person__title { font-size: 12px; color: var(--ink); margin-top: 2px; }

  .contacts {
    position: absolute; left: 24px; top: 201px;
    list-style: none;
    font-size: 12.5px; color: var(--ink);
  }
  .contacts li { display: flex; align-items: center; height: 16px; }
  .contacts svg { width: 13px; height: 13px; margin-right: 3px; }

  .company {
    position: absolute; right: 24px; top: 201px;
    text-align: right;
    font-size: 12.5px; color: var(--ink);
    line-height: 16px;
  }
  .company__name {
    font-size: 11px; font-weight: 700;
    color: var(--green);
    letter-spacing: 0.6px;
  }

  .back__mark {
    position: absolute; left: 91px; top: 95px;
    width: 82px; height: 82px;
    border-radius: 50%;
    border: 3px solid var(--green);
  }
  .back__divider {
    position: absolute; left: 181px; top: 120px;
    width: 1px; height: 40px;
    background: var(--muted);
  }
  .back__brand {
    position: absolute; left: 190px; top: 113px;
    color: var(--teal);
    font-size: 22px; font-weight: 400;
    line-height: 1.1;
    letter-spacing: 0.5px;
  }
</style>
</head>
<body>
  <section class="card card--front" aria-label="Business card front">
    <div class="front__band"></div>
    <div class="front__band-accent"></div>
    <p class="front__brand">Corvane<br>Therapeutics</p>
    <div class="front__seal"></div>

    <div class="person">
      <p class="person__name">DANIEL <span>MARSH</span></p>
      <p class="person__title">Senior Director of Marketing</p>
    </div>

    <ul class="contacts">
      <li>
        <svg viewBox="0 0 14 14" aria-hidden="true"><circle cx="7" cy="7" r="6" fill="none" stroke="#3bbfc8" stroke-width="1"/><path d="M4.5 5.5h5v1h-5zM5 7h4v2H5z" fill="#3bbfc8"/></svg>
        555-210-4837
      </li>
      <li>
        <svg viewBox="0 0 14 14" aria-hidden="true"><circle cx="7" cy="7" r="6" fill="none" stroke="#3bbfc8" stroke-width="1"/><rect x="5" y="3.8" width="4" height="6.4" rx="0.8" fill="none" stroke="#3bbfc8" stroke-width="1"/></svg>
        555-318-6402
      </li>
      <li>
        <svg viewBox="0 0 14 14" aria-hidden="true"><circle cx="7" cy="7" r="6" fill="none" stroke="#3bbfc8" stroke-width="1"/><rect x="4" y="5" width="6" height="4" fill="#3bbfc8"/><path d="M4 5l3 2.2L10 5" fill="none" stroke="#fff" stroke-width="0.8"/></svg>
        dmarsh@corvanerx.com
      </li>
    </ul>

    <div class="company">
      <p class="company__name">CORVANE THERAPEUTICS, LLC</p>
      <p>418 W Linden Avenue</p>
      <p>Fairview, GA 30999</p>
    </div>
  </section>

  <section class="card card--back" aria-label="Business card back">
    <div class="back__mark"></div>
    <div class="back__divider"></div>
    <p class="back__brand">Corvane<br>Therapeutics</p>
  </section>
</body>
</html>
```